A5 Flyer for Financial Services Business

I am after a re-design of our business flyer to fit in with our new branding style and logo colour scheme. Wanting something with a bit of designer flair that I could not create myself. I have included the flyer which I created which lacks style so dazzle me.

I want to use the same content.

Text for main body of flyer is

Are you a small business owner, tradie or TRPQ Service Provider struggling to stay on top of your bookkeeping and compliance obligations? If so we would love to help you get back on track and take control of your business finances so that you can make informed business decisions and focus on what you do best.

We have over 20 years industry experience and, as a small business ourselves, we are able to offer our clients a personal bookkeeping solution tailored to meet the needs of your business.

Accounts Payable | Accounts Receivable
Customer Invoicing
Bank and Credit Card Reconciliations
Payroll | Superannuation | Payroll Tax
Business Activity | Instalment Activity Statements
Regular Financial Reports
Vantly and Brimfolk Set-Up and Training

```html
<!DOCTYPE html>
<html lang="en">
<head>
<meta charset="utf-8">
<title>Even Ledger Financial Services – Bookkeeping Flyer</title>
<link href="https://fonts.googleapis.com/css2?family=Oswald:wght@300;400;500;600&family=Questrial&family=Poppins:wght@500&display=swap" rel="stylesheet">
<style>
  :root{
    --backdrop:#a4a4a6;
    --paper:#ffffff;
    --teal:#0b8f98;
    --teal-bright:#1aa6bd;
    --teal-deep:#0c5877;
    --ring:#0d3e58;
    --ink:#2b2b2d;
    --ink-soft:#3a3a3c;
    --footer:#404042;
    --stripe:#1fb0c9;
    --rule:#e6e6e6;
  }
  *{box-sizing:border-box;margin:0;padding:0}
  html,body{width:1200px;height:1200px;overflow:hidden}
  body{background:var(--backdrop);position:relative;font-family:'Questrial',sans-serif}
  .flyer{position:absolute;left:215px;top:54px;width:778px;height:1099px;background:var(--paper);overflow:hidden}

  .hero-photo{position:absolute;left:0;top:0;width:778px;height:545px;
    background:linear-gradient(180deg,rgba(255,255,255,0) 62%,#fff 100%),
      linear-gradient(110deg,#dfe6ea 0%,#c9d3da 30%,#e9edf0 55%,#b9c2c8 80%,#d6dde1 100%)}

  .brand{position:absolute;left:50px;top:124px;color:var(--teal)}
  .brand-name{font-size:40px;letter-spacing:3px;line-height:1;white-space:nowrap}
  .brand-sub{font-size:17px;letter-spacing:10px;line-height:1;margin-top:8px;white-space:nowrap}

  .title-row{position:absolute;left:66px;top:458px;display:flex;align-items:flex-start;gap:12px;white-space:nowrap}
  .headline{font-family:'Oswald',sans-serif;font-weight:600;color:var(--teal);font-size:76px;line-height:86px;letter-spacing:-1px}
  .tagline{font-family:'Oswald',sans-serif;font-weight:400;color:var(--ink);font-size:35px;line-height:34px;margin-top:12px}

  .side-rule{position:absolute;top:549px;height:141px;width:52px;background:var(--rule)}
  .side-rule.left{left:0}
  .side-rule.right{right:0}

  .intro{position:absolute;left:66px;top:551px;width:641px;color:var(--ink-soft);font-size:15.2px;line-height:19px;text-align:justify}
  .intro p+p{margin-top:18px}
  .intro strong{color:var(--teal);font-weight:400;-webkit-text-stroke:.4px var(--teal)}

  .service{position:absolute;width:170px;text-align:center}
  .service-badge{width:99px;height:99px;margin:0 auto;border-radius:50%;border:3px solid var(--ring);
    background:radial-gradient(circle at 50% 30%,var(--teal-bright) 0%,#1487a2 45%,var(--teal-deep) 100%);
    display:flex;align-items:center;justify-content:center}
  .service-badge svg{width:56px;height:56px}
  .service-label{margin-top:4px;font-family:'Poppins',sans-serif;font-weight:500;font-size:11.4px;line-height:16.5px;color:var(--ink);white-space:nowrap}
  .partner-names{color:#fff;font-size:17px;line-height:24px;text-align:center}

  .footer{position:absolute;left:0;top:1020px;width:778px;height:71px;background:var(--footer)}
  .footer-stripe{position:absolute;left:0;top:1091px;width:778px;height:8px;background:var(--stripe)}
  .accreditation{position:absolute;left:63px;top:988px;width:66px;height:88px;background:#fff;border:1px solid #555}
  .accreditation span{position:absolute;left:11px;top:8px;width:42px;height:42px;border-radius:50%;background:#c7d63a;border:3px solid #eee}
  .contact{position:absolute;left:160px;top:1020px;height:71px;display:flex;align-items:center;gap:14px;white-space:nowrap}
  .phone{display:flex;align-items:center;gap:6px;color:#fff;font-family:'Oswald',sans-serif;font-weight:500;font-size:44px;line-height:1;letter-spacing:-1px}
  .web{color:#fff;font-family:'Oswald',sans-serif;font-weight:300;font-size:17px;letter-spacing:-.2px;margin-top:4px}
</style>
</head>
<body>
<main class="flyer">
  <div class="hero-photo" role="img" aria-label="Photo of four businesswomen talking around a meeting table in a bright glass office"></div>

  <div class="brand">
    <div class="brand-name">EVEN LEDGER</div>
    <div class="brand-sub">Financial Services</div>
  </div>

  <div class="title-row">
    <h1 class="headline">BOOKKEEPING</h1>
    <div class="tagline">TAILORED TO YOUR<br>BUSINESS NEEDS</div>
  </div>

  <div class="side-rule left" role="img" aria-label="Fine horizontal line pattern"></div>
  <div class="side-rule right" role="img" aria-label="Fine horizontal line pattern"></div>

  <section class="intro">
    <p>Are you a <strong>small business owner, tradie or TRPQ Service Provider</strong> struggling to stay on top of your bookkeeping and compliance obligations? If so we would love to help you get back on track and take control of your business finances so that you can make informed business decisions and focus on what you do best.</p>
    <p>We have over <strong>20 years industry experience</strong> and, as a small business ourselves, we are able to offer our clients a personal bookkeeping solution tailored to meet the needs of your business.</p>
  </section>

  <!-- Services row 1 -->
  <div class="service" style="left:82px;top:713px">
    <div class="service-badge">
      <svg viewBox="0 0 56 56" fill="none" stroke="#fff" stroke-width="2.4">
        <rect x="8" y="8" width="28" height="38" rx="2"/><rect x="17" y="4" width="10" height="7" rx="2"/>
        <line x1="13" y1="22" x2="13" y2="28"/><line x1="17" y1="19" x2="17" y2="28"/><line x1="21" y1="24" x2="21" y2="28"/>
        <circle cx="16" cy="37" r="4"/>
        <rect x="28" y="24" width="20" height="26" rx="2" fill="#1487a2"/><rect x="31" y="27" width="14" height="5"/>
        <g fill="#fff" stroke="none"><rect x="31" y="35" width="3" height="3"/><rect x="36.5" y="35" width="3" height="3"/><rect x="42" y="35" width="3" height="3"/><rect x="31" y="41" width="3" height="3"/><rect x="36.5" y="41" width="3" height="3"/><rect x="42" y="41" width="3" height="3"/></g>
      </svg>
    </div>
    <div class="service-label">Accounts Payable<br>| Accounts Receivable</div>
  </div>

  <div class="service" style="left:227px;top:713px">
    <div class="service-badge">
      <svg viewBox="0 0 56 56" fill="none" stroke="#fff" stroke-width="2.4">
        <path d="M12 4h26l8 8v34H12z"/><line x1="17" y1="20" x2="40" y2="20"/><line x1="17" y1="26" x2="36" y2="26"/><line x1="17" y1="32" x2="32" y2="32"/><line x1="17" y1="38" x2="30" y2="38"/>
        <rect x="17" y="8" width="20" height="6" fill="#fff" stroke="none"/>
        <circle cx="42" cy="44" r="7" fill="#fff" stroke="none"/><path d="M38.5 44l2.5 2.5 4.5-5" stroke="#0c5877"/>
      </svg>
    </div>
    <div class="service-label">Customer Invoicing</div>
  </div>

  <div class="service" style="left:372px;top:713px">
    <div class="service-badge">
      <svg viewBox="0 0 56 56" fill="none" stroke="#fff" stroke-width="2.4">
        <rect x="6" y="10" width="38" height="24" rx="3" transform="rotate(6 25 22)"/>
        <rect x="10" y="22" width="40" height="26" rx="3" fill="#1487a2"/><line x1="10" y1="29" x2="50" y2="29"/>
        <circle cx="17" cy="40" r="3"/><line x1="24" y1="40" x2="44" y2="40" stroke-width="1.5"/>
      </svg>
    </div>
    <div class="service-label">Bank and Credit<br>Card Reconciliations</div>
  </div>

  <div class="service" style="left:517px;top:713px">
    <div class="service-badge">
      <svg viewBox="0 0 56 56" fill="none" stroke="#fff" stroke-width="2.4">
        <path d="M6 24v24h44V24L28 8z"/><path d="M6 48l16-14M50 48L34 34"/><path d="M6 24l22 16 22-16"/>
        <rect x="18" y="10" width="20" height="22" fill="#1487a2"/>
        <path d="M32 15h-5a3 3 0 000 6h2a3 3 0 010 6h-5M28 12v3M28 27v3"/>
      </svg>
    </div>
    <div class="service-label">Payroll | Superannuation<br>| Payroll Tax</div>
  </div>

  <!-- Services row 2 -->
  <div class="service" style="left:156px;top:855px">
    <div class="service-badge">
      <svg viewBox="0 0 56 56" fill="none" stroke="#fff" stroke-width="2.4">
        <rect x="8" y="12" width="38" height="22" rx="2"/><circle cx="27" cy="23" r="6"/>
        <path d="M29 20h-3a1.5 1.5 0 000 3h2a1.5 1.5 0 010 3h-3"/>
        <path d="M16 30l6 6c2 2 5 1 6-1l-4-8M22 36l-4 12M30 44l-6-8"/>
      </svg>
    </div>
    <div class="service-label">Business Activity |<br>Instalment Activity<br>Statements</div>
  </div>

  <div class="service" style="left:302px;top:855px">
    <div class="service-badge">
      <svg viewBox="0 0 56 56" fill="none" stroke="#fff" stroke-width="2.4">
        <circle cx="30" cy="18" r="11"/><path d="M34 13h-5a2.5 2.5 0 000 5h2a2.5 2.5 0 010 5h-5M30 10v3M30 23v3"/>
        <path d="M4 40h10l8 2h10a3 3 0 010 6H22M32 46l14-8a3 3 0 013 5L34 52H14l-4-2H4"/>
      </svg>
    </div>
    <div class="service-label">Regular Financial<br>Reports</div>
  </div>

  <div class="service" style="left:447px;top:855px">
    <div class="service-badge">
      <div class="partner-names">Vantly<br>Brimfolk</div>
    </div>
    <div class="service-label">Vantly and Brimfolk<br>Set-Up and Training</div>
  </div>

  <footer>
    <div class="footer"></div>
    <div class="footer-stripe"></div>
    <div class="accreditation" role="img" aria-label="Registered agent accreditation badge"><span></span></div>
    <div class="contact">
      <div class="phone">
        <svg width="34" height="38" viewBox="0 0 36 40" fill="none" stroke="var(--stripe)" stroke-width="3">
          <path d="M10 4l5 9-4 4c2 5 5 9 10 12l4-4 8 5-3 6c-14-1-25-14-26-28z" fill="var(--stripe)" stroke="none"/>
          <path d="M22 6a10 10 0 018 10M22 0a16 16 0 0114 16"/>
        </svg>
        <span>0400 318 562</span>
      </div>
      <div class="web">www.evenledgerfinancial.com.au</div>
    </div>
  </footer>
</main>
</body>
</html>
```